Corvane Capital Business Cards

These are professional business cards that are for my family office.
Put fake emails and phone numbers as of now until I finalize those components. This family office controls my families investments, assets, and future. The cards should be professional.
..
.
.
.
I just uploaded another variation of a logo I would like to see as a business card to I am inbeteen which logo to use

Target Market(s)

business

Industry/Entity Type

business

Contact Information for Business Card

Professional, wealth related, finance related.

Requirements
Must have
• Logo

```html
<!DOCTYPE html>
<html lang="en">
<head>
<meta charset="utf-8">
<title>Corvane Capital – Business Card</title>
<link href="https://fonts.googleapis.com/css2?family=Poppins:wght@400;600&display=swap" rel="stylesheet">
<style>
  :root {
    --page-bg: #e9e7e6;
    --frost-light: #f6f1f1;
    --frost-warm: #efdcdc;
    --navy: #1b1f2b;
    --band-grey: #a9abae;
    --name-grey: #b8babf;
    --ink-white: #ffffff;
    --brand-navy: #1d2233;
  }
  html, body {
    margin: 0;
    width: 1200px;
    height: 900px;
    overflow: hidden;
    background: var(--page-bg);
    font-family: "Poppins", sans-serif;
  }
  .business-card {
    position: absolute;
    left: 100px;
    top: 141px;
    width: 1000px;
    height: 618px;
    overflow: hidden;
    box-shadow: 0 10px 30px rgba(0,0,0,0.15);
  }
  .card-shapes {
    position: absolute;
    inset: 0;
  }
  .brand-block {
    position: absolute;
    left: 40px;
    top: 268px;
    width: 400px;
    text-align: center;
  }
  .brand-name {
    font-weight: 600;
    font-size: 34px;
    letter-spacing: 2px;
    color: var(--brand-navy);
    text-transform: uppercase;
    white-space: nowrap;
  }
  .contact-panel {
    position: absolute;
    left: 546px;
    top: 0;
    right: 0;
    color: var(--ink-white);
  }
  .person-name {
    position: absolute;
    top: 110px;
    margin: 0;
    font-weight: 600;
    font-size: 38px;
    line-height: 48px;
    letter-spacing: 0.5px;
    color: var(--name-grey);
    white-space: nowrap;
  }
  .person-title {
    position: absolute;
    top: 154px;
    margin: 0;
    font-size: 28px;
    line-height: 36px;
    font-weight: 400;
    white-space: nowrap;
  }
  .address {
    position: absolute;
    top: 236px;
    margin: 0;
    font-style: normal;
    font-size: 28px;
    line-height: 36.5px;
    white-space: nowrap;
  }
  .contact-list {
    position: absolute;
    top: 390px;
    margin: 0;
    padding: 0;
    list-style: none;
    font-size: 28px;
    line-height: 36.5px;
  }
  .contact-list li {
    display: flex;
    align-items: center;
    white-space: nowrap;
  }
  .contact-icon {
    width: 24px;
    height: 24px;
    margin-right: 10px;
    flex: none;
  }
</style>
</head>
<body>
  <div class="business-card">
    <svg class="card-shapes" width="1000" height="618" viewBox="0 0 1000 618">
      <defs>
        <linearGradient id="frost" x1="0" y1="0" x2="1" y2="1">
          <stop offset="0" stop-color="#efdcdc"/>
          <stop offset="0.5" stop-color="#f6f1f1"/>
          <stop offset="1" stop-color="#e8e2e0"/>
        </linearGradient>
      </defs>
      <rect class="frosted-face" width="1000" height="618" fill="url(#frost)"/>
      <path class="accent-band" d="M439,0 C505,70 512,220 470,330 L1000,330 L1000,0 Z" fill="#a9abae"/>
      <path class="navy-panel" d="M479,0 C540,80 520,220 470,330 C420,440 400,540 460,618 L1000,618 L1000,0 Z" fill="#1b1f2b"/>
    </svg>

    <div class="brand-block">
      <div class="brand-name">Corvane Capital</div>
    </div>

    <div class="contact-panel">
      <h1 class="person-name">DANIEL HARTLEY</h1>
      <p class="person-title">Managing Director</p>
      <address class="address">178, Harbour Row<br>Suite 200<br>60318,Northland</address>
      <ul class="contact-list">
        <li>
          <svg class="contact-icon" viewBox="0 0 24 24" fill="none" stroke="#fff" stroke-width="1.8" stroke-linecap="round" stroke-linejoin="round">
            <path d="M5 3h4l2 5-2.5 1.5a11 11 0 0 0 6 6L16 13l5 2v4a2 2 0 0 1-2 2A16 16 0 0 1 3 5a2 2 0 0 1 2-2z"/>
            <path d="M15 3a6 6 0 0 1 6 6M15 7a2 2 0 0 1 2 2"/>
          </svg>
          044-987 654 321
        </li>
        <li>
          <svg class="contact-icon" viewBox="0 0 24 24" fill="none" stroke="#fff" stroke-width="1.8" stroke-linejoin="round">
            <rect x="2" y="5" width="20" height="14" fill="#fff"/>
            <path d="M2 5l10 8 10-8" stroke="#1b1f2b"/>
          </svg>
          info@corvanemail.com
        </li>
        <li>
          <svg class="contact-icon" viewBox="0 0 24 24" fill="none" stroke="#fff" stroke-width="1.6">
            <circle cx="12" cy="12" r="10"/>
            <ellipse cx="12" cy="12" rx="4.5" ry="10"/>
            <path d="M2 12h20M4 7h16M4 17h16"/>
          </svg>
          www.corvanesite.com
        </li>
      </ul>
    </div>
  </div>
</body>
</html>
```